Grin Club flyer design

I am launching an office Grin Club and would like a design that sits my branding and that is appealing to customers. I have a design (I need a new one) that has all the information.
My website is maplehavendentalcarekx.com
Brand color is green. The design can be any color

Target Market(s)

Ages 30+

Industry/Entity Type

Dental

Font styles to use
Serif

Requirements
Must have
• Appealing to patients

```html
<!DOCTYPE html>
<html lang="en">
<head>
<meta charset="utf-8">
<title>Maplehaven Dental Care – Grin Club Membership</title>
<link href="https://fonts.googleapis.com/css2?family=Poppins:wght@400;500;600;700&family=Archivo+Black&family=Exo+2:wght@600;700;800&display=swap" rel="stylesheet">
<style>
  :root {
    --navy: #0f1b44;
    --green: #178a3c;
    --gold: #c2922f;
    --gold-light: #e3b75e;
    --paper: #f0fbfa;
    --white: #ffffff;
    --ink: #1d1d1d;
  }
  * { margin: 0; padding: 0; box-sizing: border-box; }
  html, body { width: 923px; height: 1200px; overflow: hidden; background: var(--navy); }
  .canvas { position: relative; width: 923px; height: 1200px; background: var(--navy); }
  .flyer { position: absolute; left: 120px; top: 118px; width: 683px; height: 964px; background: var(--paper); overflow: hidden; }

  .brand { position: absolute; top: 62px; left: 0; width: 100%; display: flex; align-items: center; justify-content: center; gap: 12px;
    font-family: "Poppins", sans-serif; font-weight: 600; font-size: 38px; line-height: 1; color: var(--green); }
  .brand-mark { width: 16px; height: 16px; border-radius: 50%; background: var(--green); }

  .intro { position: absolute; top: 192px; left: 30px; right: 30px; display: flex; align-items: center; justify-content: center; gap: 18px; color: var(--navy); }
  .intro-label { font-family: "Archivo Black", sans-serif; font-size: 22px; letter-spacing: -0.3px; }
  .club-name { font-family: "Poppins", sans-serif; font-weight: 600; font-size: 58px; line-height: 1; }

  .membership-rule { position: absolute; top: 321px; left: 0; width: 100%; height: 2px; background: var(--gold); }
  .membership-tag { position: absolute; top: 301px; left: 208px; width: 267px; height: 41px; background: var(--gold);
    border-radius: 3px; color: var(--white); font-family: "Poppins", sans-serif; font-weight: 600; font-size: 23px;
    letter-spacing: 5px; display: flex; align-items: center; justify-content: center; padding-left: 5px; }

  .plans { position: absolute; top: 359px; left: 10px; width: 663px; height: 236px; background: var(--navy); }
  .plans-heading { position: absolute; top: 7px; left: 0; width: 100%; text-align: center; color: var(--white);
    font-family: "Archivo Black", sans-serif; font-size: 18.5px; letter-spacing: 0.2px; }
  .plan { position: absolute; top: 35px; width: 156px; height: 192px; border-radius: 3px;
    background: linear-gradient(100deg, var(--gold) 0%, #cf9f3f 55%, var(--gold-light) 100%); color: var(--white); }
  .plan:nth-of-type(1) { left: 9px; }
  .plan:nth-of-type(2) { left: 172px; }
  .plan:nth-of-type(3) { left: 334px; }
  .plan:nth-of-type(4) { left: 496px; }
  .plan-title { height: 51px; padding-top: 9px; text-align: center; font-family: "Poppins", sans-serif; font-size: 15.5px; line-height: 18px; border-bottom: 1px solid rgba(255,255,255,0.35); }
  .plan-title strong { display: block; font-weight: 600; letter-spacing: -0.4px; }
  .plan-title span { display: block; font-weight: 400; }
  .plan-features { list-style: none; padding: 14px 6px 0 8px; height: 86px; font-family: "Poppins", sans-serif; font-size: 7.8px; line-height: 9px; }
  .plan-features li { position: relative; padding-left: 11px; margin-bottom: 4.5px; }
  .plan-features li::before { content: "✓"; position: absolute; left: 0; top: 0; font-size: 7.5px; }
  .plan-price { position: absolute; left: 0; top: 137px; width: 100%; height: 55px; border-top: 1px solid rgba(255,255,255,0.35);
    display: flex; align-items: baseline; justify-content: center; padding-top: 5px; font-family: "Poppins", sans-serif; }
  .plan-price b { font-weight: 600; font-size: 34px; letter-spacing: -1px; line-height: 42px; }
  .plan-price small { font-size: 11px; font-weight: 500; }
  .badge-new { position: absolute; top: 98px; right: 4px; width: 36px; height: 36px; border-radius: 50%; background: var(--navy);
    color: var(--white); font-family: "Poppins", sans-serif; font-weight: 600; font-size: 11px; display: flex; align-items: center; justify-content: center; }

  .family-photo { position: absolute; top: 619px; left: 0; width: 683px; height: 266px;
    background: linear-gradient(90deg, #cfe0ec 0%, #e6eef3 35%, #d8e6f1 60%, #c6d9e8 100%); }

  .footer { position: absolute; top: 885px; left: 0; width: 683px; height: 79px; background: var(--white); }
  .join { position: absolute; left: 50px; top: 12px; font-family: "Exo 2", sans-serif; color: var(--ink); }
  .join-title { font-weight: 700; font-size: 20px; letter-spacing: 1px; line-height: 1; }
  .join-phone { margin-top: 4px; display: flex; align-items: center; gap: 3px; color: var(--gold); font-weight: 800; font-size: 32px; line-height: 1; }
  .footer-divider { position: absolute; left: 365px; top: 16px; width: 1px; height: 44px; background: #999; }
  .financing { position: absolute; left: 374px; top: 10px; width: 300px; font-family: "Exo 2", sans-serif; color: var(--ink); }
  .financing-title { font-weight: 700; font-size: 11.5px; letter-spacing: 0.7px; }
  .partners { display: flex; align-items: center; gap: 22px; margin: 6px 0 6px 9px; }
  .partner { display: flex; align-items: center; gap: 6px; font-weight: 700; font-size: 19px; line-height: 1; color: var(--ink); }
  .partner i { width: 10px; height: 10px; border-radius: 50%; background: var(--ink); display: block; }
  .financing-note { font-family: "Poppins", sans-serif; font-size: 6.4px; font-weight: 600; }
</style>
</head>
<body>
<div class="canvas">
  <main class="flyer">
    <header class="brand">
      <span class="brand-mark"></span>
      <span class="brand-name">Maplehaven Dental Care</span>
    </header>

    <div class="intro">
      <span class="intro-label">INTRODUCING</span>
      <span class="club-name">Grin Club</span>
    </div>

    <div class="membership-rule"></div>
    <div class="membership-tag">MEMBERSHIP</div>

    <section class="plans">
      <h2 class="plans-heading">AFFORDABLE DENTAL CARE NO INSURANCE REQUIRED</h2>

      <article class="plan">
        <div class="plan-title"><strong>CORE CARE</strong><span>PREVENTIVE</span></div>
        <ul class="plan-features">
          <li>Comprehensive Annual Exam</li>
          <li>2 Professional Cleanings per Year</li>
          <li>Routine Bitewing X-rays</li>
          <li>10% Savings on Treatment</li>
        </ul>
        <div class="plan-price"><b>$39</b><small>/MONTH</small></div>
      </article>

      <article class="plan">
        <div class="plan-title"><strong>BRIGHT</strong><span>COSMETIC</span></div>
        <ul class="plan-features">
          <li>Annual In-Office Whitening (Top &amp; Bottom)</li>
          <li>Custom Whitening Trays</li>
          <li>15% Savings on Elective Treatment</li>
        </ul>
        <div class="plan-price"><b>$59</b><small>/MONTH</small></div>
      </article>

      <article class="plan">
        <div class="plan-title"><strong>TOTAL SMILE</strong><span>PERIODONTAL</span></div>
        <ul class="plan-features">
          <li>3-4 Perio Maintenance Visits per Year</li>
          <li>1 Comprehensive Exam</li>
          <li>Diagnostic X-rays</li>
          <li>15% Savings on Restorative &amp; Elective Care</li>
        </ul>
        <div class="plan-price"><b>$89</b><small>/MONTH</small></div>
      </article>

      <article class="plan">
        <div class="plan-title"><strong>SMILE REFRESH</strong><span>PACKAGE</span></div>
        <ul class="plan-features">
          <li>Cleaning + Comprehensive Exam + Whitening</li>
          <li><strong>Limited Time Offer</strong></li>
        </ul>
        <div class="badge-new">New</div>
        <div class="plan-price"><b>$499</b><small>/MONTH</small></div>
      </article>
    </section>

    <div class="family-photo" role="img" aria-label="Smiling family of four in a bright dental office"></div>

    <footer class="footer">
      <div class="join">
        <div class="join-title">JOIN GRIN CLUB TODAY!</div>
        <div class="join-phone">
          <svg width="24" height="24" viewBox="0 0 24 24" aria-hidden="true">
            <circle cx="12" cy="12" r="11" fill="#c2922f"/>
            <path d="M8.2 6.2c.4-.3 1-.3 1.3.1l1.3 1.8c.3.4.2.9-.1 1.2l-.8.8c.6 1.4 1.6 2.5 3 3.1l.8-.8c.3-.3.9-.4 1.2-.1l1.8 1.3c.4.3.5.9.1 1.3l-.9 1c-.6.6-1.5.8-2.3.5-3-1.2-5.3-3.5-6.5-6.5-.3-.8-.1-1.7.5-2.3z" fill="#fff"/>
          </svg>
          555-014-2230
        </div>
      </div>
      <div class="footer-divider"></div>
      <div class="financing">
        <div class="financing-title">FLEXIBLE FINANCING FOR TREATMENT :</div>
        <div class="partners">
          <span class="partner"><i></i>FlexPay</span>
          <span class="partner"><i></i>Plumline</span>
        </div>
        <div class="financing-note">PAYMENT PLANS AVAILABLE | *$49 Lifetime Activation Fee (Non-Refundable)</div>
      </div>
    </footer>
  </main>
</div>
</body>
</html>
```